Brightfen Business Card Redesign & Logo Update

We need to update our business cards to something more modern and fresh. Brightfen can provide the current color schemes and old design examples, but welcome creativity in helping us with this redesign. PLEASE NOTE that we no longer utilize the "tree" and/or "leaf" imagery in our branding. If able would apprecaite an update on the quality of our "words only" logo in Ai. / PNG formats too.

Target Market(s)

Investors, landowners, corporate partners, contractors

Industry/Entity Type

Environmental Restoration & Conservation

Contact Information for Business Card

Logo, persons name, title, mailing address, phone and email, website url

Font styles to use
Other font styles liked:
• Merriweather

Requirements
Nice to have
• Logo, persons name, title, mailing address, phone and email, website url, but open to ideams
Should not have
• No all back backgrounds

```html
<!DOCTYPE html>
<html lang="en">
<head>
<meta charset="utf-8">
<title>Brightfen Business Card</title>
<link href="https://fonts.googleapis.com/css2?family=Montserrat:wght@400;500;700;800&display=swap" rel="stylesheet">
<style>
  :root {
    --brand-green: #177f40;
    --brand-orange: #e87d22;
    --ink: #1c1c1c;
    --paper: #ffffff;
    --backdrop: #e6e7e8;
  }
  * { box-sizing: border-box; margin: 0; padding: 0; }
  html, body {
    width: 1200px; height: 900px; overflow: hidden;
    background: var(--backdrop);
    font-family: "Montserrat", Arial, sans-serif;
  }
  .sheet {
    position: relative; width: 1200px; height: 900px;
  }
  .card {
    position: absolute; left: 250px; width: 700px; height: 400px;
    box-shadow: 0 6px 18px rgba(0,0,0,.18);
    overflow: hidden;
  }
  .card--front { top: 30px; background: var(--brand-green); }
  .card--back { top: 470px; background: var(--paper); }

  .wordmark {
    font-weight: 800; letter-spacing: 1px; text-transform: uppercase;
    display: flex; align-items: center; gap: 14px;
  }
  .wordmark__dot { width: 14px; height: 14px; border-radius: 50%; }

  .card--front .wordmark {
    position: absolute; left: 0; right: 0; top: 0; bottom: 0;
    justify-content: center; font-size: 76px; color: var(--paper);
  }
  .card--front .wordmark__dot { background: var(--brand-orange); width: 20px; height: 20px; }

  .card--back .wordmark {
    position: absolute; right: 48px; top: 54px;
    font-size: 44px; color: var(--brand-green);
  }
  .card--back .wordmark__dot { background: var(--brand-orange); }

  .person { position: absolute; left: 48px; top: 80px; }
  .person__name { font-weight: 800; font-size: 21px; letter-spacing: .5px; }
  .person__first { color: var(--brand-green); }
  .person__last { color: var(--brand-orange); }
  .person__title { font-size: 15px; color: var(--ink); margin-top: 2px; }

  .address {
    position: absolute; right: 48px; top: 170px;
    font-size: 15px; line-height: 1.45; color: var(--ink); text-align: right;
  }

  .contacts {
    position: absolute; left: 48px; top: 236px; list-style: none;
  }
  .contacts__item {
    display: flex; align-items: center; gap: 12px;
    font-size: 17px; color: var(--ink); height: 30px;
  }
  .contacts__icon { width: 22px; height: 22px; flex: none; }

  .edge-bands { position: absolute; left: 0; bottom: 0; width: 700px; height: 60px; }
</style>
</head>
<body>
<main class="sheet">
  <section class="card card--front" aria-label="Card front">
    <div class="wordmark"><span class="wordmark__dot"></span>Brightfen</div>
  </section>

  <section class="card card--back" aria-label="Card back">
    <div class="wordmark"><span class="wordmark__dot"></span>Brightfen</div>

    <div class="person">
      <p class="person__name"><span class="person__first">DANA</span> <span class="person__last">HOLLOWAY</span></p>
      <p class="person__title">Managing Director</p>
    </div>

    <address class="address">42-07 Heron Ave 12<br>Ashby, NY 10990</address>

    <ul class="contacts">
      <li class="contacts__item">
        <svg class="contacts__icon" viewBox="0 0 22 22" aria-hidden="true">
          <circle cx="11" cy="11" r="11" fill="var(--brand-orange)"/>
          <path d="M7 6.5h2l1 2.5-1.3 1c.6 1.3 1.6 2.3 2.9 2.9l1-1.3 2.5 1v2c0 .6-.5 1-1 1C9.6 15.6 6.4 12.4 6 7.5c0-.5.4-1 1-1z" fill="#fff"/>
        </svg>555-014-2276</li>
      <li class="contacts__item">
        <svg class="contacts__icon" viewBox="0 0 22 22" aria-hidden="true">
          <circle cx="11" cy="11" r="11" fill="var(--brand-orange)"/>
          <rect x="5.5" y="7.5" width="11" height="7.5" fill="#fff"/>
          <path d="M5.5 7.5l5.5 4.2 5.5-4.2" fill="none" stroke="var(--brand-orange)" stroke-width="1"/>
        </svg>info@brightfen.com</li>
      <li class="contacts__item">
        <svg class="contacts__icon" viewBox="0 0 22 22" aria-hidden="true">
          <circle cx="11" cy="11" r="11" fill="var(--brand-orange)"/>
          <circle cx="11" cy="11" r="5.5" fill="none" stroke="#fff" stroke-width="1.3"/>
          <ellipse cx="11" cy="11" rx="2.3" ry="5.5" fill="none" stroke="#fff" stroke-width="1.1"/>
          <path d="M5.5 11h11" stroke="#fff" stroke-width="1.1"/>
        </svg>www.brightfen.com</li>
    </ul>

    <svg class="edge-bands" viewBox="0 0 700 60" aria-hidden="true">
      <polygon points="0,34 496,18 482,60 0,60" fill="var(--brand-green)"/>
      <polygon points="512,16 700,8 700,60 496,60" fill="var(--brand-orange)"/>
    </svg>
  </section>
</main>
</body>
</html>
```